A Label for an ECO Friendly Spirit Company

Design a label which can be used for vodka and gin (London Dry Gin). It should be Square type Like the Shape File you see in the uploads. KIRO means Kind Inventive Rare and Original. We want a cool and slim label that calls for eco-friendly. We want to use it for our premium
Vodka and our London Dry Gin. Please use the logo and design it in Square Type.

40%vol, 700ml

Target Market(s)

spirits and events

Industry/Entity Type

SPIRITS

Colors
00AB8E
00BBA5
67D7C9
C6EFE9
E9F9F6
59FF00
82FF00
B8FF75
E3FFCB
F4FFEA

Requirements
Must have
• Logo from KIRO, Squaee Shape

```html
<!DOCTYPE html>
<html lang="en">
<head>
<meta charset="utf-8">
<title>KIRO Vodka Label</title>
<link rel="stylesheet" href="https://fonts.googleapis.com/css2?family=Josefin+Sans:ital,wght@0,400;0,600;0,700;1,600&family=Playball&display=swap">
<style>
  :root {
    --teal-deep: #00AB8E;
    --teal: #00BBA5;
    --teal-light: #67D7C9;
    --mint: #C6EFE9;
    --mint-pale: #E9F9F6;
    --white: #ffffff;
  }
  * { margin: 0; padding: 0; box-sizing: border-box; }
  html, body { width: 744px; height: 1200px; overflow: hidden; background: var(--white); }
  .canvas { position: relative; width: 744px; height: 1200px; background: var(--white); font-family: "Josefin Sans", sans-serif; }
  .label-art { position: absolute; inset: 0; }
  .label-text { position: absolute; left: 0; width: 744px; text-align: center; color: var(--teal-deep); }
  .brand-mark { position: absolute; left: 349px; top: 398px; width: 46px; height: 46px; background: var(--teal); border-radius: 6px; }
  .brand-name { top: 470px; font-size: 38px; font-weight: 600; letter-spacing: 8px; padding-left: 8px; }
  .product-name { top: 524px; font-size: 92px; font-weight: 700; letter-spacing: 3px; line-height: 1; padding-left: 3px; }
  .grade { top: 606px; font-family: "Playball", cursive; font-size: 34px; color: var(--teal-deep); }
  .tagline { font-size: 21px; font-weight: 600; letter-spacing: 2px; }
  .tagline-first { top: 660px; color: var(--teal-deep); }
  .tagline-second { top: 690px; color: var(--teal); font-size: 18px; letter-spacing: 3px; }
  .spec { position: absolute; right: 316px; text-align: right; font-style: italic; font-weight: 600; font-size: 19px; line-height: 1; color: var(--teal-deep); }
  .spec-strength { top: 724px; }
  .spec-volume { top: 748px; }
</style>
</head>
<body>
<main class="canvas">
  <svg class="label-art" width="744" height="1200" viewBox="0 0 744 1200" aria-hidden="true">
    <defs>
      <linearGradient id="band-fill" x1="0" y1="0" x2="1" y2="0">
        <stop offset="0" stop-color="#67D7C9"/>
        <stop offset="0.35" stop-color="#00BBA5"/>
        <stop offset="1" stop-color="#00AB8E"/>
      </linearGradient>
      <radialGradient id="panel-glow" cx="0.5" cy="0.5" r="0.6">
        <stop offset="0" stop-color="#ffffff"/>
        <stop offset="1" stop-color="#E9F9F6"/>
      </radialGradient>
    </defs>
    <rect class="band" x="0" y="478" width="744" height="236" fill="url(#band-fill)"/>
    <polygon class="frame-outer" points="372,296 676,600 372,904 68,600" fill="#00AB8E"/>
    <polygon class="frame-gap" points="372,316 656,600 372,884 88,600" fill="#ffffff"/>
    <polygon class="frame-inner" points="372,326 646,600 372,874 98,600" fill="#00BBA5"/>
    <polygon class="panel" points="372,330 642,600 372,870 102,600" fill="url(#panel-glow)"/>
    <polygon class="panel-line" points="372,352 620,600 372,848 124,600" fill="none" stroke="#00BBA5" stroke-width="1.5"/>
    <line class="rule" x1="226" y1="490" x2="292" y2="490" stroke="#00AB8E" stroke-width="2"/>
    <line class="rule" x1="452" y1="490" x2="518" y2="490" stroke="#00AB8E" stroke-width="2"/>
    <line class="rule" x1="196" y1="630" x2="302" y2="630" stroke="#00AB8E" stroke-width="2"/>
    <line class="rule" x1="442" y1="630" x2="548" y2="630" stroke="#00AB8E" stroke-width="2"/>
  </svg>

  <div class="brand-mark" aria-hidden="true"></div>
  <div class="label-text brand-name">KIRO</div>
  <h1 class="label-text product-name">VODKA</h1>
  <div class="label-text grade">Premium</div>
  <div class="label-text tagline tagline-first">KIND INVENTIVE</div>
  <div class="label-text tagline tagline-second">RARE AND ORIGINAL</div>
  <div class="spec spec-strength">40%vol</div>
  <div class="spec spec-volume">700ml</div>
</main>
</body>
</html>
```